Flyer for spiritual retreat (yoga, meditation, reiki, raw food)

I would like a flyer to promote my upcoming retreat and a matching Facebook banner.

The name of the retreat is "OutBloom the Spirit" and the tagline is "retreat into you"

The activities in the retreat include daily meditation, ecstatic dance, spiritual development workshops on intuition, energy healing etc and a reiki session is included.

I would like a flyer designed to promote this, something that is editable as I will be running this multiple times and will need to adjust the flyer to add the dates etc each time.

edit: add that here will be fully catered raw food and juices, and that the retreat price includes all accomodation, meals and workshops.

Please contact me if you need further info. Please also visit my website www.marlavosk.com and www.pagenest.com/koruhaven to see my current events and promotions.

Thank you,

Marla

Reason: Hi all, thank you all for your submissions. Apologies as I am traveling and do not have much access to internet and will review your submissions and provide feedback as soon as possible. Kind regards, Marla.

Target Market(s)

People who like meditation, yoga, fans of tomas brenner and wendell marsh, those interested in personal and spiritual development.

Industry/Entity Type

Health And Wellness

Requirements
Must have
• Please put the included reiki session as as added bonus. Something like "BONUS 30 minute reiki healing session" in a little star/banner/something that stands out.
• Please emphasise the "light" part of OutBloom as I am going for a play on words between in the light and enlightenment.
• Please include placeholder text for place, location, time
• Placeholder for price
• My name (see attached file - can change colour to suit) and website (www.marlavosk.com)
Nice to have
• I prefer rounded designs, curves rather than block designs.
Should not have
• Koru Haven logo

```html
<!DOCTYPE html>
<html lang="en">
<head>
<meta charset="utf-8">
<title>OutBloom the Spirit – Retreat into You</title>
<link rel="stylesheet" href="https://fonts.googleapis.com/css2?family=Great+Vibes&family=Montserrat:wght@300;400;600;700&display=swap">
<style>
  :root {
    --page-bg: #e4e4e4;
    --paper: #ffffff;
    --purple-deep: #6c2a8e;
    --purple: #7d3a9f;
    --purple-soft: #9d5cbc;
    --ink: #1d1d1f;
    --ink-soft: #4a4550;
    --band-grey: #c9c9c9;
  }
  * { box-sizing: border-box; margin: 0; padding: 0; }
  html, body { width: 1200px; height: 1200px; overflow: hidden; }
  body { background: var(--page-bg); font-family: "Montserrat", Arial, sans-serif; color: var(--ink); }

  .flyer {
    position: absolute; left: 200px; top: 39px;
    width: 800px; height: 1122px;
    background: var(--paper); overflow: hidden;
    box-shadow: 0 10px 30px rgba(0,0,0,.18);
  }
  .flyer-shapes, .hero-photo { position: absolute; left: 0; top: 0; width: 800px; height: 1122px; }

  .client-name {
    position: absolute; left: 62px; top: 36px;
    font-family: "Great Vibes", cursive; font-weight: 400;
    font-size: 90px; line-height: 1.1; color: var(--purple);
  }

  .event-details {
    position: absolute; left: 66px; top: 150px; width: 330px;
    font-size: 15px; line-height: 21px; color: var(--ink-soft);
  }
  .event-details .detail-when { font-weight: 600; color: var(--purple-deep); }
  .event-details .detail-price { font-weight: 600; color: var(--purple-deep); }

  .photo-ring {
    position: absolute; border-radius: 50%;
    border: 2px solid var(--purple); background: var(--paper);
  }
  .photo-ring .photo { position: absolute; inset: 11px; border-radius: 50%; }
  .ring-dance { left: 21px; top: 261px; width: 250px; height: 250px; }
  .ring-dance .photo { background: linear-gradient(160deg, #f1ece6 0%, #d8c6b3 55%, #2b2a35 100%); }
  .ring-meditate { left: 226px; top: 354px; width: 214px; height: 214px; }
  .ring-meditate .photo { background: linear-gradient(180deg, #ffffff 0%, #f2ece6 60%, #e3d6cb 100%); }

  .title { position: absolute; right: 437px; text-align: right; white-space: nowrap; font-weight: 300; line-height: 1; }
  .title-bloom { top: 570px; font-size: 60px; color: #5a5560; }
  .title-spirit { top: 638px; font-size: 44px; }
  .title-retreat { top: 680px; font-size: 86px; font-weight: 400; }
  .title-into { top: 765px; font-size: 53px; }
  .title-into strong { font-weight: 700; font-size: 86px; color: var(--purple); margin-left: 6px; }

  .activities {
    position: absolute; left: 56px; top: 862px;
    list-style: none; font-size: 17.5px; line-height: 21px; font-weight: 400;
  }
  .activities li::before {
    content: ""; display: inline-block; width: 5px; height: 5px; border-radius: 50%;
    background: var(--purple); margin-right: 6px; vertical-align: middle; position: relative; top: -2px;
  }

  .bonus {
    position: absolute; left: 442px; width: 374px; top: 508px;
    text-align: center; color: #fff; line-height: 1;
  }
  .bonus-label { font-size: 36px; font-weight: 300; letter-spacing: 1px; }
  .bonus-length { font-size: 45px; font-weight: 700; margin-top: 22px; }
  .bonus-session { font-size: 38px; font-weight: 300; margin-top: 20px; line-height: 49px; }

  .host-photo {
    position: absolute; left: 507px; top: 752px; width: 240px; height: 235px;
    border-radius: 30px; border: 4px solid #fff;
    background: linear-gradient(160deg, #b9cfd6 0%, #6f9a5e 45%, #3a2b28 75%, #d48a7b 100%);
    box-shadow: 0 12px 14px -6px rgba(0,0,0,.35);
  }

  .contact-band {
    position: absolute; left: 0; top: 1019px; width: 800px; height: 53px;
    background: var(--purple); color: #fff;
    display: flex; align-items: center; font-size: 21px; font-weight: 400;
  }
  .contact-item { display: flex; align-items: center; white-space: nowrap; }
  .contact-web { margin-left: 55px; }
  .contact-social { margin-left: 30px; }
  .contact-item svg { margin-right: 9px; }
  .footer-strip {
    position: absolute; left: 0; top: 1077px; width: 800px; height: 45px; background: var(--band-grey);
  }
</style>
</head>
<body>
<main class="flyer">

  <svg class="flyer-shapes" viewBox="0 0 750 1052" preserveAspectRatio="none" aria-hidden="true">
    <defs>
      <linearGradient id="bonusPanel" x1="0" y1="0" x2="0" y2="1">
        <stop offset="0" stop-color="#6c2a8e"/>
        <stop offset="1" stop-color="#9d5cbc"/>
      </linearGradient>
    </defs>
    <path class="bonus-panel" d="M415 478 C560 470 660 410 750 285 V805 H445 Q415 805 415 775 Z" fill="url(#bonusPanel)"/>
    <path class="curve-band" d="M0 236 C90 380 230 478 400 478 C530 478 650 420 750 282" fill="none" stroke="#c9c9c9" stroke-width="16"/>
  </svg>

  <svg class="hero-photo" viewBox="0 0 750 1052" preserveAspectRatio="none" role="img" aria-label="Photograph of a woman meditating cross-legged by the sea, hand in a mudra">
    <defs>
      <linearGradient id="heroTone" x1="0" y1="0" x2="1" y2="0">
        <stop offset="0" stop-color="#ffffff"/>
        <stop offset=".4" stop-color="#f7f8fa"/>
        <stop offset=".6" stop-color="#dfe7ef"/>
        <stop offset=".8" stop-color="#e6c2ae"/>
        <stop offset="1" stop-color="#efe6e2"/>
      </linearGradient>
    </defs>
    <path d="M0 0 H750 V270 C650 410 530 468 400 468 C235 468 95 372 0 228 Z" fill="url(#heroTone)"/>
  </svg>

  <h1 class="client-name">Marla Vosk</h1>

  <section class="event-details">
    <p class="detail-when">[Date] · [Time]</p>
    <p class="detail-where">[Location / Venue address]</p>
    <p class="detail-price">[Price]</p>
    <p class="detail-includes">Includes all accommodation, meals &amp; workshops</p>
  </section>

  <div class="photo-ring ring-dance"><div class="photo" role="img" aria-label="Photograph of a dancer stretching at a ballet barre"></div></div>
  <div class="photo-ring ring-meditate"><div class="photo" role="img" aria-label="Photograph of a woman in white robe meditating"></div></div>

  <h2 class="title title-bloom">OutBloom</h2>
  <p class="title title-spirit">the Spirit</p>
  <p class="title title-retreat">Retreat</p>
  <p class="title title-into">into<strong>You</strong></p>

  <ul class="activities">
    <li>Daily meditation</li>
    <li>Ecstatic dance</li>
    <li>Spiritual development workshops</li>
    <li>Energy healing</li>
    <li>Reiki session</li>
    <li>Fully catered raw food &amp; juices</li>
  </ul>

  <section class="bonus">
    <p class="bonus-label">BONUS</p>
    <p class="bonus-length">30 minute</p>
    <p class="bonus-session">Reiki Healing<br>Session</p>
  </section>

  <div class="host-photo" role="img" aria-label="Portrait photograph of the retreat host outdoors"></div>

  <footer class="contact-band">
    <span class="contact-item contact-web">
      <svg width="18" height="18" viewBox="0 0 18 18" aria-hidden="true">
        <g fill="none" stroke="#fff" stroke-width="1.4">
          <circle cx="9" cy="9" r="7.5"/>
          <ellipse cx="9" cy="9" rx="3.5" ry="7.5"/>
          <path d="M1.5 9 H16.5 M3 5 H15 M3 13 H15"/>
        </g>
      </svg>
      www.marlavosk.com
    </span>
    <span class="contact-item contact-social">
      <svg width="22" height="22" viewBox="0 0 22 22" aria-hidden="true"><rect width="22" height="22" rx="3" fill="#fff"/></svg>
      www.pagenest.com/koruhaven
    </span>
  </footer>
  <div class="footer-strip"></div>

</main>
</body>
</html>
```